R7M Horizon Business Card Design

We need a business card created for our New Business "R7M Horizon"<br/><br/>The business card design is up to you however the following information must be on the business card:<br/><br/>Front of the business card -<br/>Email :darrenp@r7mhorizon.nz<br/>Mobile: +64 (0) 22 4870 619<br/>Website: www.r7mhorizon.nz<br/>Card Owner Name: Darren Paltrow<br/>Company Title: Business Development Manager<br/>Slogan: "The BEST of both worlds". <br/>Logo On the front attached to the design brief<br/><br/>On the back: <br/>Space on the back for 4 more versions of the logo across the bottom of the card indicating different subsidiary brands - R7M Coffee, R7M Arts, R7M ?? (The card will be used for all of these brands - We Will add the extra subsidiary logos to the design once the design is finished (We are a graphics design team). <br/><br/>Other than that we want a premium feeling logo that remains universally usable depending on the business entity that we are using the card for. The use of bright bold colours would be great but we still want the card to feel premium.
Target Market(s)
Gift Design and Manufacturing Companies
Contact Information for Business Card
Front of the business card -
Email :darrenp@r7mhorizon.nz
Mobile: +64 (0) 22 4870 619
Website: www.r7mhorizon.nz
Card Owner Name: Darren Paltrow
Company Title: Business Development Manager
Slogan: "The BEST of both worlds".
Logo On the front attached to the design brief

```html
<!DOCTYPE html>
<html lang="en">
<head>
<meta charset="utf-8">
<title>R7M Horizon Business Card</title>
<link href="https://fonts.googleapis.com/css2?family=Open+Sans:wght@400;600;700&display=swap" rel="stylesheet">
<style>
  :root {
    --brand-blue: #3949a0;
    --ink-dark: #2b2b2b;
    --ink-grey: #5a5a5a;
    --paper: #ffffff;
    --backdrop: #e9e8e6;
  }
  * { box-sizing: border-box; margin: 0; padding: 0; }
  html, body {
    width: 1200px; height: 900px; overflow: hidden;
    background: var(--backdrop);
    font-family: "Open Sans", Arial, sans-serif;
  }
  .stage { position: relative; width: 1200px; height: 900px; }
  .card {
    position: absolute; width: 580px; height: 332px;
    box-shadow: 0 10px 28px rgba(0,0,0,0.18);
  }
  .card--back { left: 110px; top: 100px; background: var(--brand-blue); color: var(--paper); }
  .card--front { left: 510px; top: 470px; background: var(--paper); }

  .brand { position: absolute; display: flex; align-items: center; gap: 14px; font-weight: 700; letter-spacing: 1px; }
  .brand__dot { width: 26px; height: 26px; border-radius: 50%; border: 4px solid currentColor; }
  .card--back .brand { left: 0; right: 0; top: 118px; justify-content: center; font-size: 40px; }
  .tagline { position: absolute; left: 0; right: 0; top: 240px; text-align: center; font-size: 17px; letter-spacing: 0.5px; }
  .tagline strong { font-weight: 700; }

  .card--front .brand { left: 0; right: 0; top: 66px; justify-content: center; font-size: 38px; color: var(--brand-blue); }
  .owner { position: absolute; right: 310px; top: 200px; text-align: right; }
  .owner__name { font-size: 22px; font-weight: 700; color: var(--brand-blue); letter-spacing: 0.5px; }
  .owner__title { font-size: 15px; color: var(--ink-grey); margin-top: 2px; }
  .divider { position: absolute; left: 290px; top: 190px; width: 1.5px; height: 78px; background: var(--brand-blue); }
  .contacts { position: absolute; left: 306px; top: 188px; list-style: none; font-size: 14.5px; color: var(--ink-dark); }
  .contacts li { display: flex; align-items: center; gap: 8px; height: 27px; }
  .contacts svg { width: 14px; height: 14px; fill: var(--brand-blue); flex: none; }
</style>
</head>
<body>
<main class="stage">
  <section class="card card--back">
    <div class="brand"><span class="brand__dot"></span><span>R7M Horizon</span></div>
    <p class="tagline">The <strong>BEST</strong> of both worlds</p>
  </section>

  <section class="card card--front">
    <div class="brand"><span class="brand__dot"></span><span>R7M Horizon</span></div>
    <div class="owner">
      <p class="owner__name">DARREN PALTROW</p>
      <p class="owner__title">Business Development Manager</p>
    </div>
    <span class="divider"></span>
    <ul class="contacts">
      <li><svg viewBox="0 0 14 14"><path d="M4 0h6a1 1 0 0 1 1 1v12a1 1 0 0 1-1 1H4a1 1 0 0 1-1-1V1a1 1 0 0 1 1-1zm0.5 1.5v9h5v-9z"/></svg>+64 (0) 22 4870 619</li>
      <li><svg viewBox="0 0 14 14"><path d="M0 3h14v1L7 8 0 4zM0 5.5l7 4 7-4V11H0z"/></svg>darrenp@r7mhorizon.nz</li>
      <li><svg viewBox="0 0 14 14"><circle cx="7" cy="7" r="6.5"/><path d="M1 7h12M7 1c2 2 2 10 0 12M7 1c-2 2-2 10 0 12" stroke="#fff" stroke-width="1" fill="none"/></svg>www.r7mhorizon.nz</li>
    </ul>
  </section>
</main>
</body>
</html>
```